Halcyon Electrical Services Website

'Mossgrove Electrical Services' is a leading electrician company based in Hertfordshire. We are a VORTIN approved and registered company in the UK. We are also registered to carry out electrical installations under Part P of the building regulations. As part of a wide range of electrical services, we have professional expertise in installation testing (landlords, periodic, insurance, emergency lighting & fire alarms) rewires, installations, electrical maintenance, security systems & portable appliance testing (PAT). We provide a bespoke service to suite the needs of High End clients so the site must reflect the type of clientele we are targeting

WE ARE A SMALL COMPANY AND ARE LOOKING FOR THE DESIGNERS TO ALSO IMPLEMENT THIS ONTO OUR DOMAIN NAME SO ITS A FULLY FUNCTIONAL FOR OUR CLIENTS WHEN WE FINISH THIS SIMPLE PROJECT

Target Market(s)

Estate Agents, High End Clients that require intallations in Multi Million pound houses

Industry/Entity Type

Electrician

Font styles to use
Serif
Sans Serif
Other font styles liked:
• Chose an elegant professional font

Requirements
Must have
• please look at www.mossgroveelectrical.example (the current old site is down, and will go live in 24-48 hours so please get the content from there)

Luxury design, a wow factor when high end clients logon

the logo is Blue so a blue colour these for the branding is essential. We are open to your design ideas around the logo.

VORTIN and Part P and Wiring Assurance Board are safety regulations so please add the logos a place on the site together.
Nice to have
• your creative input
Should not have
• to many conflicting colours, too many horrible bright colours

```html
<!DOCTYPE html>
<html lang="en">
<head>
<meta charset="utf-8">
<title>Mossgrove Electrical Services</title>
<link rel="stylesheet" href="https://fonts.googleapis.com/css2?family=Open+Sans:wght@400;600;700&family=Oswald:wght@400;500&display=swap">
<style>
:root{
  --bg:#dde5ee;
  --page:#ffffff;
  --blue:#1f5ba8;
  --blue-dark:#143f78;
  --ink:#2a2f36;
  --muted:#6b727c;
  --line:#d7dce2;
  --nav:#2b2d31;
  --nav-line:#45484d;
  --hero-a:#2c4f80;
  --hero-b:#8ea3ba;
  --hero-c:#c9b79a;
  --pill:#23466f;
}
*{box-sizing:border-box;margin:0;padding:0}
html,body{width:720px;height:1200px;overflow:hidden}
body{background:linear-gradient(180deg,#eef2f6,var(--bg));font-family:"Open Sans",Arial,sans-serif;color:var(--ink);position:relative}
.page{position:absolute;left:24px;top:0;width:672px;height:1200px;background:var(--page);box-shadow:0 0 12px rgba(20,40,70,.15)}
.abs{position:absolute}

.brand{left:58px;top:44px;font-size:14px;font-weight:600;color:var(--ink);white-space:nowrap}

.call{left:400px;top:58px;display:flex;align-items:center;gap:8px}
.call svg{width:22px;height:22px}
.call small{display:block;font-size:10px;color:var(--muted)}
.call strong{display:block;font-size:13px;color:var(--ink)}

.nav{left:350px;top:120px;width:346px;height:22px;background:var(--nav);display:flex}
.nav a{flex:1;font-size:10px;color:#e8ebef;text-decoration:none;text-align:center;line-height:22px;border-left:1px solid var(--nav-line);white-space:nowrap}
.nav a.active{background:var(--blue);border-left:none}

.hero{left:24px;top:142px;width:672px;height:268px;background:linear-gradient(110deg,var(--hero-c) 0%,var(--hero-b) 35%,var(--hero-a) 70%,#1b3560 100%)}
.hero-text{left:430px;top:312px;color:#fff;font-size:11px;text-transform:uppercase;line-height:1.5;letter-spacing:.3px;white-space:nowrap}
.hero-text b{font-weight:700}
.dots{left:340px;top:394px;display:flex;gap:6px}
.dots i{width:7px;height:7px;border-radius:50%;background:rgba(255,255,255,.55)}
.dots i.on{background:#fff}

.section-title{left:70px;top:424px;font-family:"Oswald",sans-serif;font-size:17px;font-weight:500;color:var(--ink);text-transform:uppercase}
.section-rule{left:70px;top:449px;width:580px;height:1px;background:var(--line)}
.section-rule::before{content:"";position:absolute;left:0;top:-1px;width:86px;height:3px;background:var(--blue)}

.card{width:182px}
.card-img{width:182px;height:74px;border:1px solid var(--line)}
.card h3{font-size:12.5px;font-weight:600;color:var(--blue);margin:8px 0 4px}
.card p,.card li{font-size:8px;color:var(--muted);line-height:1.45}
.card ul{list-style:none}
.card li::before{content:"";display:inline-block;width:5px;height:5px;background:#e2a531;border-radius:50%;margin-right:5px;vertical-align:1px}
.more-btn{position:absolute;left:48px;width:58px;height:14px;border-radius:8px;background:var(--pill);color:#fff;font-size:7.5px;text-align:center;line-height:14px}

.welcome-bar{left:70px;top:908px;width:372px;height:24px;background:var(--blue);color:#fff;font-family:"Oswald",sans-serif;font-size:13px;line-height:24px;padding-left:10px;text-transform:uppercase}
.welcome-sub{left:70px;top:944px;font-size:10px;font-weight:600;color:var(--ink)}
.welcome-copy{left:70px;top:964px;width:372px}
.welcome-copy p{font-size:8.5px;color:var(--muted);line-height:1.55;margin-bottom:8px}
.welcome-more{left:402px;top:1118px;font-size:9px;color:var(--blue);font-weight:600}

.side-box{left:466px;width:186px;border:1px solid var(--line);background:#fafbfc}
.side-box h4{font-size:10.5px;font-weight:600;color:var(--ink);text-align:center;padding:8px 0;border-bottom:1px solid var(--line)}
.badge-shape{margin:14px auto;width:110px;height:34px;border-radius:4px;background:#e6ebf1;border:2px solid var(--blue)}
.field{display:block;margin:8px 14px 0;height:16px;border:1px solid var(--line);background:#fff;font-size:8px;color:#9aa1aa;line-height:14px;padding-left:6px}
.subscribe{display:block;margin:10px 14px 12px auto;width:60px;height:16px;background:var(--blue);color:#fff;font-size:8.5px;text-align:center;line-height:16px}

.footer-rule{left:24px;top:1136px;width:672px;height:1px;background:var(--line)}
.foot-badges{left:44px;top:1148px;display:flex;gap:12px}
.foot-badges .b1{width:40px;height:42px;background:#4d9a3a;border-radius:4px}
.foot-badges .b2{width:44px;height:42px;background:#f1f3f5;border:2px solid #9aa3ad}
.copy{left:430px;top:1162px;font-size:7.5px;color:var(--muted)}
.social{left:590px;top:1176px;display:flex;gap:5px}
.social i{width:14px;height:14px;background:var(--blue);border-radius:2px}
</style>
</head>
<body>
<div class="page"></div>

<div class="abs brand">Mossgrove Electrical Services Ltd</div>

<div class="abs call">
  <svg viewBox="0 0 24 24"><circle cx="12" cy="12" r="12" fill="#1f5ba8"/><path d="M8.5 6.5l2 2-1.2 1.6c.8 1.7 2 2.9 3.6 3.6l1.6-1.2 2 2-1.3 2c-4.2-.4-7.7-3.9-8.1-8.1z" fill="#fff"/></svg>
  <div><small>Call Us On</small><strong>+44 (0) 1462 555 019</strong></div>
</div>

<nav class="abs nav">
  <a class="active" href="#">Home</a><a href="#">About Us</a><a href="#">Services</a><a href="#">Technicians</a><a href="#">Contact Us</a>
</nav>

<div class="abs hero" role="img" aria-label="Electrician at work wiring a distribution board inside a timber stud wall"></div>
<div class="abs hero-text">We are electrician company,<br>we are a <b>VORTIN</b> approved and registered<br>company in the UK.</div>
<div class="abs dots"><i class="on"></i><i></i><i></i><i></i></div>

<h2 class="abs section-title">Our Services</h2>
<div class="abs section-rule"></div>

<div class="abs card" style="left:70px;top:462px;height:180px">
  <div class="card-img" role="img" aria-label="Multimeter and test leads on an installation" style="background:linear-gradient(135deg,#e0b93c,#3a3d42)"></div>
  <h3>Installation Testing</h3>
  <ul><li>Landlords</li><li>Periodic</li><li>Insurance</li><li>Emergency lighting</li><li>Fire alarms</li></ul>
  <span class="more-btn" style="top:166px">Read More</span>
</div>
<div class="abs card" style="left:270px;top:462px;height:180px">
  <div class="card-img" role="img" aria-label="Coloured electrical cables" style="background:linear-gradient(90deg,#3c6fb8,#c9a33a 50%,#8a5a32)"></div>
  <h3>Rewires</h3>
  <p>Careful certified work for homes and estates, carried out to current regulations by our qualified team of electricians.</p>
  <span class="more-btn" style="top:166px">Read More</span>
</div>
<div class="abs card" style="left:470px;top:462px;height:180px">
  <div class="card-img" role="img" aria-label="Wall sockets and switches installed" style="background:linear-gradient(135deg,#f2f2f2,#b9bec5)"></div>
  <h3>Installations</h3>
  <p>New circuits, lighting and sockets fitted neatly in fine homes, planned around each room and tested before handover.</p>
  <span class="more-btn" style="top:166px">Read More</span>
</div>

<div class="abs card" style="left:70px;top:684px;height:180px">
  <div class="card-img" role="img" aria-label="Electrician servicing wiring" style="background:linear-gradient(135deg,#2e4c7a,#9aa9bc)"></div>
  <h3>Electrical Maintenance</h3>
  <p>Planned checks and repairs that keep every system safe, reliable and compliant for owners, tenants and agents alike.</p>
  <span class="more-btn" style="top:166px">Read More</span>
</div>
<div class="abs card" style="left:270px;top:684px;height:180px">
  <div class="card-img" role="img" aria-label="Security keypad and door entry panel" style="background:linear-gradient(135deg,#d8dbe0,#7d848e)"></div>
  <h3>Security Systems</h3>
  <p>Alarms, door entry and camera systems designed discreetly for large residences and fitted by our own trusted staff.</p>
  <span class="more-btn" style="top:166px">Read More</span>
</div>
<div class="abs card" style="left:470px;top:684px;height:180px">
  <div class="card-img" role="img" aria-label="Portable appliance tester in use" style="background:linear-gradient(135deg,#e6c23a,#4a4d52)"></div>
  <h3>Portable Appliance Testing (PAT)</h3>
  <p>Fast appliance checks with clear labels and records, arranged at a time that suits your home or your business.</p>
  <span class="more-btn" style="top:166px">Read More</span>
</div>

<h2 class="abs welcome-bar">Welcome to Mossgrove Electrical</h2>
<p class="abs welcome-sub">Trusted Electricians Across Hertfordshire</p>
<div class="abs welcome-copy">
  <p>We deliver bespoke electrical work for fine homes and estate agents across Hertfordshire, with every installation tested, certified and finished to the standard our clients expect from a premium service.</p>
  <p>Our approved team handles rewires, maintenance, security systems and appliance testing, working quietly and cleanly so that each property is left exactly as we found it, only safer.</p>
  <p>From a single circuit to a full rewire of a large residence, we plan each job with care and report clearly at every stage.</p>
</div>
<a class="abs welcome-more">More &raquo;</a>

<aside class="abs side-box" style="top:906px">
  <h4>Approved and Registered</h4>
  <div class="badge-shape"></div>
</aside>
<aside class="abs side-box" style="top:1002px">
  <h4>Newsletter</h4>
  <span class="field">Name</span>
  <span class="field">Email</span>
  <span class="subscribe">Subscribe</span>
</aside>

<div class="abs footer-rule"></div>
<div class="abs foot-badges"><span class="b1"></span><span class="b2"></span></div>
<p class="abs copy">&copy; 2013 www.mossgroveelectrical.example All Rights Reserved</p>
<div class="abs social"><i></i><i></i><i></i><i></i></div>
</body>
</html>
```